Home Staging Company needs business card design

We're a home staging company called Brightly Settled Home Staging. We would like a business card design that includes aqua and gray. Our current logo of house within chair is fine but I find we almost always use the logo in one color. I'll upload images of front and back of our current card and our logo. Note that we have dropped "Solutions" from our company name and don't want to include it on the card.

Target Market(s)

Realtors and homeowners - people interested in selling their homes

Contact Information for Business Card

Marisol Thistlewood
Brightly Settled Home Staging
757-555-0193
www.brightlysettled.com
marisol@brightlysettled.com

Font styles to use
Serif
Script

Requirements
Must have
• My logo and contact details
• UPDATE***
• I forgot to say that the company name should be included on the front of the card somehow.

```html
<!DOCTYPE html>
<html lang="en">
<head>
<meta charset="utf-8">
<title>Brightly Settled Home Staging – Business Card</title>
<link rel="stylesheet" href="https://fonts.googleapis.com/css2?family=Playfair+Display:wght@400&family=Roboto+Condensed:wght@400&family=Questrial&display=swap">
<style>
  :root {
    --backdrop: #bfbfbf;
    --charcoal: #3a3e42;
    --charcoal-deep: #2f3336;
    --aqua: #4aa8b4;
    --aqua-text: #4fb1bd;
    --paper: #f2f2f2;
    --ink-light: #e9ecee;
    --ink-dark: #3b3f43;
  }
  html, body {
    margin: 0;
    padding: 0;
    width: 1200px;
    height: 576px;
    overflow: hidden;
    background: var(--backdrop);
  }
  .sheet {
    position: relative;
    width: 1200px;
    height: 576px;
  }
  .card {
    position: absolute;
    top: 138px;
    width: 484px;
    height: 294px;
    border-radius: 11px;
    overflow: hidden;
  }

  /* Back side */
  .card-back {
    left: 82px;
    background: var(--charcoal);
  }
  .back-wordmark {
    position: absolute;
    left: 0;
    right: 0;
    top: 106px;
    text-align: center;
    font-family: "Playfair Display", serif;
    font-weight: 400;
    color: var(--ink-light);
  }
  .back-wordmark .name {
    display: block;
    font-size: 38px;
    line-height: 1;
    letter-spacing: -0.5px;
  }
  .back-wordmark .tagline {
    display: block;
    margin-top: 10px;
    font-size: 15px;
    letter-spacing: 8px;
    text-transform: uppercase;
  }
  .back-url {
    position: absolute;
    left: 0;
    right: 0;
    top: 266px;
    text-align: center;
    font-family: "Questrial", sans-serif;
    font-size: 12.5px;
    color: var(--aqua-text);
  }

  /* Front side */
  .card-front {
    left: 602px;
    background: var(--aqua);
  }
  .front-shape {
    position: absolute;
    inset: 0;
  }
  .person {
    position: absolute;
    left: 28px;
    top: 31px;
  }
  .person-name {
    margin: 0;
    font-family: "Roboto Condensed", sans-serif;
    font-weight: 400;
    font-size: 19px;
    color: #ffffff;
  }
  .person-title {
    margin: 6px 0 0;
    font-family: "Questrial", sans-serif;
    font-size: 10.5px;
    color: #ffffff;
  }
  .contact-list {
    position: absolute;
    left: 28px;
    top: 204px;
    margin: 0;
    padding: 0;
    list-style: none;
    font-family: "Questrial", sans-serif;
    font-size: 12px;
    color: #ffffff;
  }
  .contact-list li {
    display: flex;
    align-items: center;
    height: 17.5px;
  }
  .contact-list svg {
    width: 10px;
    height: 10px;
    margin-right: 12px;
    fill: none;
    stroke: #ffffff;
    stroke-width: 1.3;
  }
  .front-brand {
    position: absolute;
    left: 310px;
    top: 0;
    width: 174px;
    height: 294px;
  }
  .brand-dot {
    position: absolute;
    left: 4px;
    top: 102px;
    width: 72px;
    height: 72px;
    border-radius: 50%;
    background: var(--aqua);
  }
  .brand-name {
    position: absolute;
    left: 104px;
    top: 46px;
    height: 204px;
    writing-mode: vertical-rl;
    text-align: center;
    font-family: "Playfair Display", serif;
    font-weight: 400;
    font-size: 19px;
    line-height: 1.25;
    color: var(--ink-dark);
  }
</style>
</head>
<body>
<main class="sheet">

  <section class="card card-back" aria-label="Card back">
    <div class="back-wordmark">
      <span class="name">Brightly Settled</span>
      <span class="tagline">Home Staging</span>
    </div>
    <div class="back-url">www.brightlysettled.com</div>
  </section>

  <section class="card card-front" aria-label="Card front">
    <svg class="front-shape" viewBox="0 0 484 294" preserveAspectRatio="none" aria-hidden="true">
      <path d="M298 0 H316 C290 90 290 200 310 294 H296 C276 200 274 90 298 0 Z" fill="var(--charcoal-deep)"/>
      <path d="M310 0 H484 V294 H316 C294 200 292 90 310 0 Z" fill="var(--paper)"/>
    </svg>

    <div class="person">
      <h1 class="person-name">Marisol Thistlewood</h1>
      <p class="person-title">Managing Director</p>
    </div>

    <ul class="contact-list">
      <li>
        <svg viewBox="0 0 10 10"><path d="M1 3 Q5 0 9 3 L8 4.5 L6.5 3.8 L6.5 3 Q5 2.5 3.5 3 L3.5 3.8 L2 4.5 Z M2.5 5 H7.5 L8.5 9 H1.5 Z"/></svg>
        757-555-0193
      </li>
      <li>
        <svg viewBox="0 0 10 10"><circle cx="5" cy="5" r="4"/><ellipse cx="5" cy="5" rx="1.8" ry="4"/><path d="M1 5 H9"/></svg>
        www.brightlysettled.com
      </li>
      <li>
        <svg viewBox="0 0 10 10"><rect x="0.8" y="2" width="8.4" height="6"/><path d="M0.8 2 L5 5.5 L9.2 2"/></svg>
        marisol@brightlysettled.com
      </li>
    </ul>

    <div class="front-brand">
      <span class="brand-dot" aria-hidden="true"></span>
      <div class="brand-name">Brightly Settled<br>Home Staging</div>
    </div>
  </section>

</main>
</body>
</html>
```